Bright Step Path Flyer, eyecatching

Hi,
To give you an idea of the business for design purposes, #BrighttStepPath is predominantly a recruitment and people development business, ran by me dedicated to training & assisting others in achieving extra income (pt or f/t) around their current commitments, people also have the opportunity to build their own business brand with my support. My brand colours are Red, White and Black, and I would like to incorporate the following text;

#BrightStepPath

Recruiting now! Start today & start earning!

Would you like an extra income, for…
A holiday?…A new car?…Lifestyle changes?
(Can you put a tick box or something similar adjacent to each)

Are you facing…
Redundancy? Birth of a new child? Hefty bills?

If so, I have the solution.

Contact Yvonne Darcott today: (can you insert the appropriate icon for each of the contact details)
Tel: 07419 604172
Twitter: @Bright_StepPath
Email: Yvonne@brightsteppath-example.co.uk
Facebook: www.facebook-example.com/yvonbrightsteppath

Target Market(s)

Women aged 25-45 years, possibly busy mums too, wanting to earn additinal income to allow them more choices, be it family time, money, new challenge, meeting new people, personal development

Industry/Entity Type

Health And Wellness

Font styles to use
Serif
Sans Serif
Decorative
Script

Colors
ec1f27
ffffff
000000

Requirements
Must have
• My heels logo, be clear concise and eye catching, I also have the following strap line if you wish to use;
• Empowering other to achieve
• Also I have attached a closeup picture of myself but would ideally only like half my face to appear (leftside) similar to the other picture posted - if you can
Nice to have
• Perhaps adding other forms of graphics, or the 3rd picture I have attached with myself...possibly just the shoes though
Should not have
• Too many colours

```html
<!DOCTYPE html>
<html lang="en">
<head>
<meta charset="utf-8">
<title>Bright Step Path – Recruiting Now</title>
<link rel="stylesheet" href="https://fonts.googleapis.com/css2?family=Advent+Pro:wght@300;400&family=Open+Sans:wght@600;700&family=Roboto+Condensed:wght@400;700&display=swap">
<style>
  :root {
    --red: #ec1f27;
    --white: #ffffff;
    --black: #000000;
    --ink: #1a1a1f;
    --panel: #1d1d24;
  }
  html, body { margin: 0; padding: 0; overflow: hidden; background: var(--white); }
  .flyer {
    position: relative;
    width: 847px;
    height: 1200px;
    overflow: hidden;
    background: var(--white);
    font-family: "Open Sans", Arial, sans-serif;
    color: var(--ink);
  }
  .portrait-column { position: absolute; left: 0; top: 0; width: 444px; height: 1200px; }
  .portrait-backdrop { position: absolute; left: 0; top: 0; display: block; }

  .recruiting {
    position: absolute; left: 28px; top: 404px;
    font-family: "Advent Pro", Arial, sans-serif; font-weight: 300;
    font-size: 46px; line-height: 56px; letter-spacing: 1px; color: var(--black); margin: 0;
    display: flex; align-items: center; gap: 8px; white-space: nowrap;
  }
  .recruiting svg { display: block; flex: none; }

  .question {
    position: absolute; left: 0; width: 444px;
    font-family: "Open Sans", Arial, sans-serif; font-weight: 700;
    font-size: 15px; letter-spacing: 0.5px; color: var(--white);
    text-align: center; margin: 0;
  }
  .need-grid { position: absolute; left: 60px; width: 340px; display: flex; justify-content: space-between; }
  .need { width: 110px; text-align: center; }
  .need svg { display: block; margin: 0 auto 10px; }
  .need-label {
    font-weight: 600; font-size: 13px; line-height: 1.25; color: var(--white);
    text-transform: uppercase; margin: 0;
  }

  .contact-list { position: absolute; left: 32px; top: 978px; margin: 0; padding: 0; list-style: none; color: var(--white); }
  .contact-list li { display: flex; align-items: center; gap: 10px; font-weight: 700; font-size: 17px; line-height: 28px; white-space: nowrap; }
  .contact-list li svg { display: block; flex: none; }
  .contact-list .phone { font-size: 38px; line-height: 54px; gap: 12px; }
  .social-mark { width: 13px; height: 13px; background: var(--white); display: inline-block; flex: none; margin: 0 4px; }

  .brand { position: absolute; left: 444px; top: 46px; width: 403px; text-align: center; }
  .brand-name {
    font-family: "Advent Pro", Arial, sans-serif; font-weight: 400;
    font-size: 50px; color: var(--red); margin: 0; line-height: 1;
  }
  .brand-sub { font-family: "Roboto Condensed", Arial, sans-serif; font-size: 19px; margin: 8px 0 0; color: var(--black); }
  .heels { position: absolute; left: 520px; top: 190px; display: block; }

  .start {
    position: absolute; left: 444px; top: 492px; width: 403px; text-align: center; margin: 0;
    font-family: "Advent Pro", Arial, sans-serif; font-weight: 400; font-size: 34px; line-height: 40px; color: var(--black);
  }

  .provides-title {
    position: absolute; left: 478px; top: 654px; margin: 0;
    font-family: "Roboto Condensed", Arial, sans-serif; font-weight: 700; font-size: 21px; color: var(--black);
  }
  .benefits { position: absolute; left: 488px; top: 706px; width: 316px; margin: 0; padding: 0; list-style: none; }
  .benefits li { position: relative; height: 66px; }
  .benefit-title { font-family: "Advent Pro", Arial, sans-serif; font-weight: 400; font-size: 21px; line-height: 24px; display: block; color: var(--black); }
  .benefit-note { font-family: "Roboto Condensed", Arial, sans-serif; font-size: 11px; display: block; text-transform: uppercase; color: var(--black); }
  .benefits li::after {
    content: ""; position: absolute; right: 0; top: 7px;
    width: 7px; height: 7px; border: 2px solid var(--red); border-radius: 50%;
  }

  .contact-card { position: absolute; left: 444px; top: 1022px; width: 403px; text-align: center; }
  .contact-heading { font-family: "Roboto Condensed", Arial, sans-serif; font-weight: 700; font-size: 22px; margin: 0; color: var(--black); }
  .contact-name { font-family: "Advent Pro", Arial, sans-serif; font-weight: 400; font-size: 34px; margin: 0; line-height: 38px; letter-spacing: 1px; color: var(--black); }
  .tagline { font-family: "Roboto Condensed", Arial, sans-serif; font-size: 19px; margin: 4px 0 0; color: var(--black); }
</style>
</head>
<body>
<main class="flyer">

  <section class="portrait-column">
    <svg class="portrait-backdrop" width="444" height="1200" viewBox="0 0 444 1200">
      <defs>
        <linearGradient id="portrait-tone" x1="0" y1="0" x2="1" y2="1">
          <stop offset="0" stop-color="#5a5a5a"/>
          <stop offset="0.45" stop-color="#bdbdbd"/>
          <stop offset="0.75" stop-color="#e2e2e2"/>
          <stop offset="1" stop-color="#9a9a9a"/>
        </linearGradient>
      </defs>
      <rect class="portrait" x="0" y="0" width="444" height="960" fill="url(#portrait-tone)" role="img" aria-label="Black and white close-up portrait of the founder, left half of the face"/>
      <polygon class="light-band" points="0,380 444,350 444,480 0,512" fill="#ffffff" opacity="0.35"/>
      <polygon class="dark-overlay" points="0,512 444,470 444,960 0,960" fill="var(--panel)" opacity="0.88"/>
      <polygon class="contact-band" points="0,922 444,950 444,1200 0,1200" fill="var(--panel)"/>
    </svg>

    <h1 class="recruiting">RECRUITING NOW
      <svg width="26" height="40" viewBox="0 0 26 40" aria-hidden="true"><polyline points="4,4 20,20 4,36" fill="none" stroke="var(--black)" stroke-width="7"/></svg>
    </h1>

    <p class="question" style="top:532px;">WOULD YOU LIKE AN EXTRA INCOME FOR...</p>
    <div class="need-grid" style="top:576px;">
      <div class="need">
        <svg width="62" height="62" role="img" aria-label="Red holiday icon"><circle cx="31" cy="31" r="28" fill="var(--red)"/></svg>
        <p class="need-label">A holiday?</p>
      </div>
      <div class="need">
        <svg width="62" height="62" role="img" aria-label="Red lifestyle changes icon"><circle cx="31" cy="31" r="28" fill="var(--red)"/></svg>
        <p class="need-label">Lifestyle<br>changes?</p>
      </div>
      <div class="need">
        <svg width="62" height="62" role="img" aria-label="Red car icon"><rect x="4" y="14" width="54" height="34" rx="6" fill="var(--red)"/></svg>
        <p class="need-label">A new car?</p>
      </div>
    </div>

    <p class="question" style="top:726px;">ARE YOU FACING...</p>
    <div class="need-grid" style="top:766px;">
      <div class="need">
        <svg width="62" height="72" role="img" aria-label="Red no job sign"><rect x="6" y="6" width="50" height="60" rx="4" fill="var(--red)"/></svg>
        <p class="need-label">Redundancy?</p>
      </div>
      <div class="need">
        <svg width="62" height="72" role="img" aria-label="Red expectant mother icon"><rect x="18" y="4" width="26" height="64" rx="13" fill="var(--red)"/></svg>
        <p class="need-label">Birth of a<br>new child?</p>
      </div>
      <div class="need">
        <svg width="62" height="72" role="img" aria-label="Red bills icon"><rect x="8" y="8" width="46" height="56" rx="3" fill="var(--red)" transform="rotate(-10 31 36)"/></svg>
        <p class="need-label">Hefty bills?</p>
      </div>
    </div>

    <ul class="contact-list">
      <li class="phone">
        <svg width="34" height="34" viewBox="0 0 34 34" aria-hidden="true"><circle cx="17" cy="17" r="15" fill="none" stroke="var(--white)" stroke-width="2.5"/><path d="M11 9 l4 0 l1 5 l-2 2 q2 4 5 5 l2 -2 l5 1 l0 4 q-10 1 -15 -15z" fill="var(--white)"/></svg>
        07419 604172
      </li>
      <li>
        <svg width="22" height="16" viewBox="0 0 22 16" aria-hidden="true"><rect x="1" y="1" width="20" height="14" fill="none" stroke="var(--white)" stroke-width="2"/><polyline points="1,1 11,9 21,1" fill="none" stroke="var(--white)" stroke-width="2"/></svg>
        Yvonne@brightsteppath-example.co.uk
      </li>
      <li><span class="social-mark"></span>yvonbrightsteppath</li>
      <li><span class="social-mark"></span>@Bright_StepPath</li>
    </ul>
  </section>

  <header class="brand">
    <p class="brand-name">#BrightStepPath</p>
    <p class="brand-sub">Recruitment &amp; People Development</p>
  </header>

  <svg class="heels" width="270" height="180" role="img" aria-label="Sketch of a pair of black and red high heels">
    <defs>
      <linearGradient id="heel-tone" x1="0" y1="0" x2="1" y2="1">
        <stop offset="0" stop-color="#f2f2f2"/>
        <stop offset="1" stop-color="#f6dcdd"/>
      </linearGradient>
    </defs>
    <rect width="270" height="180" rx="8" fill="url(#heel-tone)"/>
  </svg>

  <p class="start">START TODAY!<br>START EARNING!</p>

  <h2 class="provides-title">OUR SUCCESSFUL BRAND PROVIDES:</h2>
  <ul class="benefits">
    <li><span class="benefit-title">FLEXIBLE WORKING HOURS</span><span class="benefit-note">From home</span></li>
    <li><span class="benefit-title">EXCITING BONUS</span><span class="benefit-note">&amp; Rewards schemes</span></li>
    <li><span class="benefit-title">BESPOKE TRAINING</span><span class="benefit-note">&amp; Development</span></li>
    <li><span class="benefit-title">PROGRESSION</span><span class="benefit-note">Opportunities</span></li>
  </ul>

  <section class="contact-card">
    <h3 class="contact-heading">CONTACT</h3>
    <p class="contact-name">YVONNE DARCOTT</p>
    <p class="tagline">Empowering others to achieve</p>
  </section>

</main>
</body>
</html>
```